Lendquay wedsite and logo refresh

We are looking for someone to refresh the look and feel of Lendquay.co.nz we are moving it towards a more traditional brokerage.

Target Market(s)

30 to 55 year old professionals

Coding

Coded - Design and coding required

Number of Pages Required

3 page

Requirements
Nice to have
• we are needing a modern professional look

```html
<!DOCTYPE html>
<html lang="en">
<head>
<meta charset="utf-8">
<title>Lendquay</title>
<link href="https://fonts.googleapis.com/css2?family=Oswald:wght@400;500;600&family=Montserrat:ital,wght@0,400;0,500;1,400&display=swap" rel="stylesheet">
<style>
:root{
  --brand:#e8431f;
  --brand-dark:#b3230e;
  --ink:#1e1e1e;
  --text:#555;
  --muted:#8a8a8a;
  --grey-band:#e7e6e7;
  --footer:#262626;
  --white:#fff;
}
*{margin:0;padding:0;box-sizing:border-box}
html,body{width:1200px;height:3853px;overflow:hidden;background:var(--white)}
body{font-family:'Montserrat',sans-serif;color:var(--text)}
.page{position:relative;width:1200px;height:3853px;overflow:hidden}
.abs{position:absolute}
.head{font-family:'Oswald',sans-serif;font-weight:500;text-transform:uppercase;color:var(--ink)}
.label{font-family:'Oswald',sans-serif;font-weight:500;color:var(--brand);font-size:16px;letter-spacing:1.5px;text-transform:uppercase}
.center{left:0;width:1200px;text-align:center}
.btn{position:absolute;background:var(--brand);color:var(--white);font-family:'Oswald',sans-serif;font-weight:500;text-transform:uppercase;font-size:17px;display:flex;align-items:center;justify-content:center}
.side{position:absolute;width:20px}
.side .line{position:absolute;left:9px;width:1px;background:#bbb}
.side .txt{position:absolute;left:-40px;width:100px;text-align:center;transform:rotate(-90deg);font-family:'Oswald',sans-serif;font-size:10px;letter-spacing:1px;color:#555;text-transform:uppercase}
/* header */
.social-dot{position:absolute;width:12px;height:12px;border-radius:50%;background:var(--brand)}
.logo{font-family:'Oswald',sans-serif;font-weight:400;color:var(--brand);text-transform:uppercase;letter-spacing:-0.5px}
.nav{left:111px;top:88px;width:977px;height:75px;background:var(--brand);z-index:2}
.nav a{position:absolute;top:26px;color:var(--white);font-family:'Oswald',sans-serif;font-weight:500;font-size:15px;text-decoration:none;text-transform:uppercase}
.nav .active::after{content:"";position:absolute;left:0;right:0;top:30px;height:3px;background:var(--white)}
.signup{position:absolute;left:763px;top:13px;width:176px;height:47px;background:var(--white);color:var(--brand);font-family:'Oswald',sans-serif;font-weight:500;font-size:18px;display:flex;align-items:center;justify-content:center;text-transform:uppercase}
/* hero */
.hero{left:0;top:114px;width:1200px;height:558px;background:linear-gradient(100deg,#4a4d52 0%,#6f7377 30%,#8d9aa6 55%,#3d4750 80%,#2b2f33 100%)}
.hero h1{position:absolute;left:107px;top:130px;font-family:'Oswald',sans-serif;font-weight:500;font-size:66px;line-height:73px;color:var(--white);text-transform:uppercase}
/* services */
.svc{position:absolute;top:1343px;width:304px;height:328px;overflow:hidden}
.svc .ttl{position:absolute;left:0;width:100%;text-align:center;font-family:'Oswald',sans-serif;font-weight:500;font-size:27px;color:var(--white);text-transform:uppercase}
/* team */
.quote{font-style:italic;font-size:14px;line-height:26px;color:#6a6a6a;text-align:center}
/* mission */
.mcard{position:absolute;top:2688px;width:226px;height:280px;background:var(--white);box-shadow:0 0 0 1px #e4e4e4,0 2px 6px rgba(0,0,0,.08);text-align:center}
.mcard .circ{position:absolute;left:56px;top:-30px;width:114px;height:114px;border-radius:50%;background:#ebebeb;display:flex;align-items:center;justify-content:center}
.mcard h3{position:absolute;left:0;width:100%;top:94px;font-family:'Oswald',sans-serif;font-weight:500;font-size:17px;line-height:25px;color:var(--brand);text-transform:uppercase}
.mcard p{position:absolute;left:20px;right:20px;top:160px;font-size:14px;line-height:25.5px;color:#777}
.mcard.on{background:var(--brand);box-shadow:none}
.mcard.on .circ{background:var(--white)}
.mcard.on h3,.mcard.on p{color:var(--white)}
/* footer */
.footer{left:0;top:3467px;width:1200px;height:386px;background:var(--footer)}
.fh{position:absolute;font-family:'Oswald',sans-serif;font-weight:500;font-size:16px;color:var(--white);text-transform:uppercase}
.flist{position:absolute;list-style:none;font-size:15.5px;line-height:25.7px;color:var(--white)}
.flist li::before{content:"»";margin-right:14px}
</style>
</head>
<body>
<div class="page">

  <!-- top header -->
  <div class="social-dot" style="left:124px;top:32px"></div>
  <div class="social-dot" style="left:169px;top:32px"></div>
  <div class="social-dot" style="left:212px;top:32px"></div>
  <div class="social-dot" style="left:257px;top:32px"></div>
  <div class="abs logo" style="left:0;width:1200px;text-align:center;top:12px;font-size:40px">Lendquay</div>
  <div class="abs" style="left:877px;top:29px;display:flex;align-items:center;gap:5px;font-family:'Oswald',sans-serif;font-size:15px;color:#333">
    <svg width="15" height="15" viewBox="0 0 16 16"><circle cx="8" cy="8" r="7" fill="none" stroke="#e8431f" stroke-width="1.6"/><circle cx="8" cy="6.5" r="2.3" fill="#e8431f"/><path d="M3.8 12.5c1.5-2.6 6.9-2.6 8.4 0" stroke="#e8431f" stroke-width="1.6" fill="none"/></svg>LOG IN</div>
  <div class="abs" style="left:993px;top:18px;width:40px;height:40px;border-radius:50%;background:#2b4c96"></div>
  <div class="abs" style="left:1046px;top:28px;font-family:'Oswald',sans-serif;font-size:15px;color:#333">ENG ▾</div>

  <nav class="abs nav">
    <a class="active" href="#" style="left:82px">Home</a>
    <a href="#" style="left:172px">About Us</a>
    <a href="#" style="left:288px">Careers</a>
    <a href="#" style="left:398px">Media</a>
    <a href="#" style="left:490px">Support</a>
    <a href="#" style="left:603px">Contact&nbsp; Us</a>
    <div class="signup">Sign&nbsp; up for free</div>
  </nav>

  <!-- hero -->
  <div class="abs hero" role="img" aria-label="Photo of colleagues in an office discussing a plan">
    <h1>No Obligations<br>No Fees<br>No Worries</h1>
    <div class="btn" style="left:108px;top:377px;width:307px;height:56px">btn-white transform-upper</div>
    <div class="side" style="left:1148px;top:100px;height:250px">
      <div class="line" style="top:0;height:130px;background:rgba(255,255,255,.6)"></div>
      <div class="txt" style="top:168px;color:rgba(255,255,255,.7)">Scroll down</div>
    </div>
  </div>

  <!-- about -->
  <div class="side" style="left:72px;top:750px;height:358px">
    <div class="line" style="top:0;height:118px"></div>
    <div class="txt" style="top:172px">About us</div>
    <div class="line" style="top:240px;height:118px"></div>
  </div>
  <div class="abs center label" style="top:768px">About us</div>
  <div class="abs center head" style="top:793px;font-size:42px">Who is Lendquay?</div>
  <p class="abs" style="left:180px;width:840px;top:864px;text-align:center;font-size:16px;line-height:26px">Lendquay CEO Daniel Hart doesn’t like door knockers. They have a habit of showing up during dinner, or interrupting family time. He decided there must be a better way to field offers,“Our goal is to get major banks, insurance companies, utility companies and other consumer service suppliers fighting for the consumer’s business.”With Lendquay, you can submit a form with a few basic details, and get a range of representative offers back in under 90 seconds.</p>
  <div class="btn" style="left:486px;top:1020px;width:228px;height:50px">Learn more</div>

  <!-- services -->
  <div class="abs" style="left:0;top:1157px;width:1200px;height:686px;background:var(--grey-band)"></div>
  <div class="side" style="left:1127px;top:1322px;height:355px">
    <div class="line" style="top:0;height:115px"></div>
    <div class="txt" style="top:168px">Services</div>
    <div class="line" style="top:240px;height:115px"></div>
  </div>
  <div class="abs center label" style="top:1248px">Services</div>
  <div class="abs center head" style="top:1273px;font-size:42px">Find and compare rates</div>

  <div class="svc" style="left:123px;background:linear-gradient(160deg,#6b6b6b,#2c2c2c 60%,#1a1a1a)" role="img" aria-label="Photo of hands holding a rising chart of percentage symbols">
    <div class="ttl" style="top:218px">Mortgage rates</div>
    <svg class="abs" style="left:144px;top:262px" width="16" height="34" viewBox="0 0 16 34"><path d="M8 34V2M2 9l6-7 6 7" stroke="#fff" stroke-width="1.5" fill="none"/></svg>
  </div>
  <div class="svc" style="left:448px;background:var(--brand)">
    <div class="ttl" style="top:28px">Personal finance</div>
    <p class="abs" style="left:36px;right:36px;top:80px;text-align:center;color:#fff;font-size:15.5px;line-height:26px">Lorem ipsum dolor sit amet, consectetur adipiscing elit, sed do eiusmod tempor incididunt ut labore et dolore magna aliqua Ut enim ad minim veniam.</p>
    <svg class="abs" style="left:144px;top:262px" width="16" height="34" viewBox="0 0 16 34"><path d="M8 0v32M2 25l6 7 6-7" stroke="#fff" stroke-width="1.5" fill="none"/></svg>
  </div>
  <div class="svc" style="left:773px;background:linear-gradient(135deg,#8fa3b5,#5d6d7c 45%,#8a1f24 70%,#3b3f46)" role="img" aria-label="Photo of a family beside a red car">
    <div class="ttl" style="top:218px">Vehicle finance</div>
    <svg class="abs" style="left:144px;top:262px" width="16" height="34" viewBox="0 0 16 34"><path d="M8 34V2M2 9l6-7 6 7" stroke="#fff" stroke-width="1.5" fill="none"/></svg>
  </div>
  <div class="btn" style="left:486px;top:1698px;width:228px;height:50px">View all services</div>

  <!-- team -->
  <div class="abs" style="left:0;top:1843px;width:1200px;height:570px;background:linear-gradient(100deg,#e8431f 0%,#dc3a18 50%,#b3230e 100%)"></div>
  <div class="side" style="left:32px;top:1975px;height:355px">
    <div class="line" style="top:0;height:115px;background:rgba(255,255,255,.5)"></div>
    <div class="txt" style="top:168px;color:rgba(255,255,255,.8)">Meet our team</div>
    <div class="line" style="top:240px;height:115px;background:rgba(255,255,255,.5)"></div>
  </div>
  <div class="abs center label" style="top:1934px;color:#fff">Our people</div>
  <div class="abs center head" style="top:1958px;font-size:42px;color:#fff">Meet the team</div>
  <div class="abs" style="left:77px;top:2030px;width:1045px;height:295px;background:rgba(255,255,255,.22);overflow:hidden">
    <p class="quote abs" style="left:60px;width:180px;top:20px;color:rgba(255,255,255,.55)">Driven to frustration by door to door hawkers in January 2016 putting the power in hands of the consumer include a specialised company, where</p>
    <p class="quote abs" style="left:825px;width:180px;top:20px;color:rgba(255,255,255,.55)">Daniel co-founded with the power in the trade prior enterprises and building products cladding system.</p>
  </div>
  <div class="abs" style="left:275px;top:2030px;width:650px;height:295px;background:#fff">
    <p class="quote abs" style="left:65px;right:65px;top:20px">Driven to frustration by door to door hawkers, Daniel co-founded Lendquay in January 2016, with the aim of putting the power in the hands of the consumer.An innovator by trade, Daniel’s prior enterprises include a specialised courier van rental agency, and a building products company, where he designed a revolutionary cladding system.</p>
    <div class="abs" style="left:296px;top:160px;width:58px;height:58px;border-radius:50%;background:#2a2a2a;border:2px solid #eee" role="img" aria-label="Portrait of the CEO"></div>
    <div class="abs" style="left:0;width:650px;text-align:center;top:245px;font-family:'Oswald',sans-serif;font-weight:500;font-size:16px;color:var(--brand)">DANIEL HART , <i style="font-size:13px;font-weight:400">CEO</i></div>
  </div>

  <!-- mission -->
  <div class="side" style="left:1127px;top:2573px;height:355px">
    <div class="line" style="top:0;height:115px"></div>
    <div class="txt" style="top:168px">Our mission</div>
    <div class="line" style="top:240px;height:115px"></div>
  </div>
  <div class="abs center label" style="top:2512px">Our mission</div>
  <div class="abs center head" style="top:2535px;font-size:42px">Why Lendquay?</div>
  <div class="abs center" style="top:2601px;font-size:17px;color:#444">Our mission is to put the power in the hands of the consumer</div>

  <div class="mcard on" style="left:121px">
    <div class="circ"><svg width="56" height="56" viewBox="0 0 56 56" fill="none" stroke="#e8431f" stroke-width="2"><path d="M6 40l10-8h14l8-6 4 3-12 13H14l-6 6"/><path d="M28 6l3 6 6 1-4.5 4 1 6-5.5-3-5.5 3 1-6L19 13l6-1z"/></svg></div>
    <h3>Great rates &amp;<br>incentives</h3>
    <p>Receive the great rates and incentives hassle-free - Lendquay does the shopping around for you.</p>
  </div>
  <div class="mcard" style="left:365px">
    <div class="circ"><svg width="56" height="56" viewBox="0 0 56 56" fill="none" stroke="#e8431f" stroke-width="2"><path d="M28 50S14 32 14 22a14 14 0 0128 0c0 10-14 28-14 28z"/><circle cx="28" cy="22" r="5"/><ellipse cx="28" cy="50" rx="14" ry="3"/></svg></div>
    <h3>Any time,<br>any where</h3>
    <p>Get notifications and review representative offers wherever you are with your personal.</p>
  </div>
  <div class="mcard" style="left:609px">
    <div class="circ"><svg width="56" height="56" viewBox="0 0 56 56" fill="none" stroke="#e8431f" stroke-width="2"><rect x="14" y="6" width="28" height="44" rx="4"/><path d="M19 28c5-7 13-7 18 0-5 7-13 7-18 0z"/><circle cx="28" cy="28" r="2.5"/></svg></div>
    <h3>Privacy is<br>important</h3>
    <p>Your private information is disclosed only when you follow up on representative offers from a service.</p>
  </div>
  <div class="mcard" style="left:853px">
    <div class="circ"><svg width="56" height="56" viewBox="0 0 56 56" fill="none" stroke="#e8431f" stroke-width="2"><rect x="8" y="26" width="9" height="22"/><path d="M17 28l8-12V8c5 0 7 4 6 12h12c3 0 4 3 3 5l-4 18c-1 3-3 5-6 5H17"/></svg></div>
    <h3>No fees,<br>no obligations</h3>
    <p>Receive the great rates and incentives hassle-free - Lendquay does the shopping around for you.</p>
  </div>

  <!-- contact -->
  <div class="abs" style="left:0;top:3064px;width:1200px;height:403px;background:linear-gradient(90deg,#ececec 0%,#f1efee 45%,#e9e3dd 60%,#d9d4cf 100%)"></div>
  <div class="abs" style="left:600px;top:3064px;width:600px;height:403px;background:linear-gradient(90deg,rgba(240,238,237,0),#d8d2cc 40%,#5b4a44 65%,#cfc9c2 100%)" role="img" aria-label="Photo of a woman in a kitchen looking at her phone"></div>
  <div class="side" style="left:50px;top:3090px;height:355px">
    <div class="line" style="top:0;height:115px"></div>
    <div class="txt" style="top:168px;color:#aaa">Get in touch</div>
    <div class="line" style="top:240px;height:115px"></div>
  </div>
  <div class="abs label" style="left:108px;top:3155px">Contact us</div>
  <div class="abs head" style="left:108px;top:3177px;font-size:42px">Get in touch</div>
  <p class="abs" style="left:108px;width:490px;top:3244px;font-size:17px;line-height:26px;color:#555">Lorem ipsum dolor sit amet, consectetur adipiscing elit, sed do eiusmod tempor incididunt ut labore et dolore magna aliqua.</p>
  <div class="btn" style="left:108px;top:3342px;width:171px;height:49px">Get a quote</div>

  <!-- footer -->
  <footer class="abs footer">
    <div class="abs logo" style="left:113px;top:110px;font-size:40px">Lendquay</div>
    <div class="social-dot" style="left:122px;top:203px;background:#fff"></div>
    <div class="social-dot" style="left:169px;top:203px;background:#fff"></div>
    <div class="social-dot" style="left:216px;top:203px;background:#fff"></div>
    <div class="social-dot" style="left:264px;top:203px;background:#fff"></div>

    <div class="fh" style="left:379px;top:71px">Quicks links</div>
    <ul class="flist" style="left:379px;top:105px">
      <li>Home</li><li>About Us</li><li>Careers</li><li>Media</li><li>Support</li><li>Contact&nbsp; Us</li>
    </ul>
    <div class="fh" style="left:600px;top:71px">Our services</div>
    <ul class="flist" style="left:600px;top:105px">
      <li>Mortgage</li><li>Personal Finance</li><li>Vehicle Finance</li><li>Commercial Finance</li><li>Insurance</li><li>Vehicle Leasing</li>
    </ul>
    <div class="fh" style="left:877px;top:71px">Newsletters</div>
    <div class="abs" style="left:877px;top:131px;width:209px;height:44px;background:#fff;font-size:12px;color:#333;padding:14px 11px">Enter The Email</div>
    <div class="btn" style="left:877px;top:185px;width:209px;height:45px;font-size:17px">Subscribe</div>

    <div class="abs" style="left:108px;top:293px;width:978px;height:1px;background:#444"></div>
    <div class="abs" style="left:0;width:1200px;text-align:center;top:310px;font-family:'Oswald',sans-serif;font-size:16px;color:#fff">( C ) Copyrights 2020 <span style="color:var(--brand)">LENDQUAY</span> &nbsp; | &nbsp; All Rights Reserved</div>
  </footer>
</div>
</body>
</html>
```